Harbor Loom Floors Letterhead

Letterhead used for business reasons. It must be editable and easy to use.

Address is 2715 W. Pelican Lane Englewood FL 34187 - 941.382.6519

```html
<!DOCTYPE html>
<html lang="en">
<head>
<meta charset="utf-8">
<title>Harbor Loom Floors Letterhead</title>
<link href="https://fonts.googleapis.com/css2?family=Lato:wght@400&family=Open+Sans:wght@400;600&family=Outfit:wght@500&display=swap" rel="stylesheet">
<style>
  :root {
    --backdrop: #e9eaec;
    --paper: #ffffff;
    --accent: #e08a25;
    --text: #6f6f72;
    --muted: #8a8580;
    --ink: #2b2b2e;
    --rule: #9a9a9a;
    --ghost: #f1f1f3;
    --sign-area: #f4f4f5;
  }
  * { box-sizing: border-box; margin: 0; padding: 0; }
  html, body { width: 999px; height: 1200px; overflow: hidden; background: var(--backdrop); }
  .letterhead {
    position: absolute; left: 86px; top: 20px;
    width: 827px; height: 1160px;
    background: var(--paper); overflow: hidden;
    font-family: "Open Sans", sans-serif; color: var(--text);
  }
  .brand-name {
    position: absolute; left: 58px; top: 72px;
    font-family: "Lato", sans-serif; font-weight: 400;
    font-size: 31px; color: var(--accent); letter-spacing: 0.2px;
  }
  .company-contact {
    position: absolute; left: 545px; top: 82px;
    font-family: "Lato", sans-serif; font-size: 14px; color: var(--muted);
    list-style: none;
  }
  .company-contact li { display: flex; gap: 6px; line-height: 18px; margin-bottom: 10px; }
  .company-contact svg { flex: none; margin-top: 1px; }
  .header-rule { position: absolute; top: 175px; height: 1.5px; }
  .header-rule.accent { left: 58px; width: 215px; background: var(--accent); }
  .header-rule.plain { left: 279px; width: 489px; background: var(--rule); }

  .sender { position: absolute; left: 73px; top: 278px; }
  .sender-name { font-size: 22px; font-weight: 600; color: var(--accent); line-height: 28px; }
  .sender-role { font-size: 12px; color: var(--ink); margin-top: 1px; }
  .sender-details { list-style: none; margin-top: 14px; font-size: 14px; color: var(--ink); }
  .sender-details li { line-height: 23px; }
  .sender-details .label { display: inline-block; width: 29px; color: var(--accent); font-weight: 600; }

  .letter-date { position: absolute; right: 75px; top: 399px; font-size: 14px; color: var(--ink); }

  .letter-body { position: absolute; left: 75px; top: 471px; width: 677px; }
  .letter-body p {
    font-size: 13.6px; line-height: 21.6px; text-align: justify;
    margin-bottom: 21.6px;
  }
  .signature { position: absolute; left: 91px; top: 824px; width: 118px; height: 74px; background: var(--sign-area); border-radius: 4px; }
  .signatory { position: absolute; left: 75px; top: 909px; font-family: "Outfit", sans-serif; font-weight: 500; font-size: 20px; color: var(--ink); }

  .ghost-name {
    position: absolute; left: 330px; top: 1010px;
    font-family: "Lato", sans-serif; font-weight: 400; font-size: 150px;
    color: var(--ghost); white-space: nowrap; line-height: 1;
  }
  .footer-band { position: absolute; left: 0; bottom: 0; width: 335px; height: 16px; background: var(--accent); }
</style>
</head>
<body>
<main class="letterhead">
  <div class="ghost-name" aria-hidden="true">Harbor Loom</div>

  <header>
    <div class="brand-name">Harbor Loom Floors</div>
    <ul class="company-contact">
      <li>
        <svg width="17" height="17" viewBox="0 0 17 17" aria-hidden="true"><rect width="17" height="17" rx="2" fill="#e08a25"/><path d="M5 4.2c.4-.3.9-.2 1.1.2l1 1.7c.2.4.1.8-.2 1l-.7.5c.4 1 1.3 1.9 2.3 2.3l.5-.7c.2-.3.7-.4 1-.2l1.7 1c.4.2.5.7.2 1.1l-.8.9c-.5.5-1.3.5-2.2.1C7 11.2 5.8 10 4.9 8.1 4.5 7.2 4.5 6.4 5 5.9z" fill="#fff"/></svg>
        <span>941.382.6519</span>
      </li>
      <li>
        <svg width="17" height="17" viewBox="0 0 17 17" aria-hidden="true"><rect width="17" height="17" rx="2" fill="#e08a25"/><path d="M8.5 3a3.6 3.6 0 0 0-3.6 3.6c0 2.6 3.6 6.6 3.6 6.6s3.6-4 3.6-6.6A3.6 3.6 0 0 0 8.5 3z" fill="#fff"/><circle cx="8.5" cy="6.6" r="1.4" fill="#e08a25"/></svg>
        <span>2715 W. Pelican Lane Englewood<br>FL 34187</span>
      </li>
    </ul>
    <div class="header-rule accent"></div>
    <div class="header-rule plain"></div>
  </header>

  <section class="sender">
    <h1 class="sender-name">James Doe</h1>
    <p class="sender-role">Chief Director</p>
    <ul class="sender-details">
      <li><span class="label">A :</span>4986 Northwest Washington, DC 20025</li>
      <li><span class="label">W :</span>www.companywebsite.com</li>
      <li><span class="label">P :</span>+00 123 456 78</li>
      <li><span class="label">M :</span>office@harborloomfloors.com</li>
    </ul>
  </section>

  <p class="letter-date">12 December, 2025</p>

  <article class="letter-body">
    <p>Lorem ipsum dolor sit amet, consectetuer adipiscing elit, sed diam nonummy nibh euismod tincidunt ut laoreet dolore magna aliquam erat volutpat. Ut wisi enim ad minim veniam, quis nostrud exerci tation ullamcorper suscipit lobortis nisl ut aliquip ex ea commodo consequat. Duis autem vel eum iriure dolor in hendrerit in vulputate velit esse molestie consequat, vel illum dolore eu feugiat nulla facilisis at vero eros et accumsan et iusto odio dignissim qui blandit praesent luptatum zzril delenit augue duis dolore te feugait nulla facilisi.</p>
    <p>Lorem ipsum dolor sit amet, cons ectetuer adipiscing elit, sed diam nonummy nibh euismod tincidunt ut laoreet dolore magna aliquam erat volutpat. Ut wisi enim ad minim veniam, quis nostrud exerci tation ullamcorper suscipit lobortis nisl ut aliquip ex ea commodo consequat.</p>
    <p>Lorem ipsum dolor sit amet, consectetuer adipiscing elit, sed diam nonummy nibh euismod tincidunt ut laoreet dolore magna aliquam eratveniam, quis nostrud exerci tation ullamcorper suscipit lobortis nisl ut aliquip ex ea commodo consequat. Lorem ipsum dolor sit zamet, consectetuer adipiscing elit, sed diam nonummy nibh euismod tincidunt.</p>
  </article>

  <div class="signature" role="img" aria-label="Handwritten signature"></div>
  <p class="signatory">Mr. Jone Smith</p>

  <div class="footer-band"></div>
</main>
</body>
</html>
```